PDF flyer for our companies' two main products: Food processing machines.

PDF flyer with showcasing two products. Flyer can be one page per product, or both products on the same page.

Product #1: Labeled "Ribbon blenders".
Showing a photo of the machine, and the details/features offered with that machine. Product description must also say: "Sizes available; 2 Cu Ft. - 450 Cu Ft."

Product #2: Labeled: " Auger hoppers / Screw feeders"
Showing a photo of the machine, and the details/features offered with that machine.

SEE UPLOADED IMAGES; "Ribbon Blenders EXAMPLE FLYER".
& "Auger Hoppers / Screw Conveyors EXAMPLE FLYER" for a rough idea of what we are looking for.

Target Market(s)

Copackers, Packing houses, Food manufacturers, protein powder producers,

Industry/Entity Type

Commercial Food processing / packing / mixing equipment

Font styles to use
Serif

Colors
0054AA
0677BA
7BADD7
CADEEF
E8F1F8

Requirements
Must have
• Company logo on top of flyer.
Nice to have
• I would like for the flyer to show some stock images of common ingredients, similar to the images uploaded.
Should not have
• Pictures with background. Backgrounds must be removed from provides photos. "clipping path"

```html
<!DOCTYPE html>
<html lang="en">
<head>
<meta charset="utf-8">
<title>Keelworth Equipment – Product Flyers</title>
<link href="https://fonts.googleapis.com/css2?family=Merriweather:wght@700&family=Open+Sans:wght@400;600&display=swap" rel="stylesheet">
<style>
:root{
  --blue-deep:#0054AA;
  --blue-mid:#0677BA;
  --blue-soft:#7BADD7;
  --blue-pale:#CADEEF;
  --blue-mist:#E8F1F8;
  --ink:#111;
  --stage:#e9ecef;
  --steel-hi:#d9dcdf;
  --steel-lo:#8f959b;
}
*{margin:0;padding:0;box-sizing:border-box}
html,body{width:1200px;height:674px;overflow:hidden;background:var(--stage)}
body{position:relative;font-family:"Open Sans",Arial,sans-serif;color:var(--ink)}
.page{position:absolute;top:54px;width:401px;height:566px;background:linear-gradient(#fff,#f3f5f7);overflow:hidden;box-shadow:0 2px 8px rgba(0,0,0,.25)}
.page--blenders{left:182px}
.page--feeders{left:617px}
.band{position:absolute;left:0;width:401px}
.band--top{top:0;height:70px}
.band--bottom{bottom:0;height:80px}
.brand{position:absolute;top:12px;right:36px;display:flex;align-items:center;gap:4px;font-family:"Merriweather",Georgia,serif;font-weight:700;font-size:9px;color:#fff;letter-spacing:.5px}
.brand__dot{width:6px;height:6px;border-radius:50%;background:#fff}
.title{position:absolute;top:70px;left:0;width:100%;text-align:center;font-family:"Merriweather",Georgia,serif;font-weight:700;font-size:13px;letter-spacing:.2px;color:var(--ink)}
.card{position:absolute;background:linear-gradient(#fff 35%,var(--blue-pale) 75%,var(--blue-soft));padding:8px 9px}
.card--box{top:112px;width:104px;height:125px;border-radius:6px}
.card--round{width:112px;height:112px;border-radius:50%;padding:22px 10px 0 24px}
.card h3{font-family:"Merriweather",Georgia,serif;font-weight:700;font-size:6px;margin-bottom:6px;letter-spacing:.2px}
.card ul{list-style:none}
.card li{position:relative;padding-left:10px;font-size:3.7px;line-height:4.5px;margin-bottom:4.4px}
.card li::before{content:"";position:absolute;left:0;top:0.5px;width:3px;height:3px;border:0.6px solid var(--blue-mid);border-radius:50%}
.card li::after{content:"";position:absolute;left:1.3px;top:1.8px;width:1px;height:1px;background:var(--blue-mid);border-radius:50%}
.photo{position:absolute;border-radius:50%;border:2px solid var(--blue-deep)}
.machine{position:absolute;border-radius:4px;background:linear-gradient(135deg,var(--steel-hi),var(--steel-lo))}
.spec{position:absolute;border-collapse:collapse;background:#fff;font-family:Arial,"Open Sans",sans-serif}
.spec td{border:0.5px solid #000;padding:0 1px;white-space:nowrap}
.spec--blenders{left:68px;top:451px;width:267px;font-size:3.4px;line-height:4.6px}
.spec--blenders tr:first-child td{font-weight:600}
.spec--feeders{left:72px;top:485px;width:258px;font-size:4.8px;line-height:6.7px;font-family:"Open Sans",Arial,sans-serif}
.spec--feeders .c{text-align:center}
</style>
</head>
<body>

<section class="page page--blenders">
  <svg class="band band--top" viewBox="0 0 401 70" preserveAspectRatio="none" aria-hidden="true">
    <path d="M0 0H401V20C300 40 230 60 150 48C90 40 40 24 0 26Z" fill="var(--blue-deep)"/>
    <path d="M0 28C40 22 90 40 150 50C230 62 300 44 401 24" fill="none" stroke="var(--blue-mid)" stroke-width="1.2"/>
  </svg>
  <div class="brand"><span class="brand__dot"></span>KEELWORTH</div>
  <h1 class="title">RIBBON BLENDERS</h1>

  <div class="card card--box" style="left:86px">
    <h3>STANDARD FEATURES</h3>
    <ul>
      <li>304 Stainless Steel Construction</li>
      <li>Pre-wired control panel with; batch timer, on/off switch, emergency stop button</li>
      <li>Food grade compression shaft seals</li>
      <li>Safety sensor on lid for automatic shutoff when opened</li>
      <li>Air acutated discharge valve</li>
      <li>1 Piece hinged lid with safety granting</li>
      <li>Power options; 220v/480v</li>
      <li>24" Standard discharge height</li>
      <li>Castor wheels on 53cf units and smaller</li>
    </ul>
  </div>
  <div class="card card--box" style="left:212px">
    <h3>OPTIONS</h3>
    <ul>
      <li>Dual hinged lids available on custom order</li>
      <li>Knife gate style discharge available on custom orders</li>
      <li>Air pure seals available on custom orders</li>
      <li>316 Stainless materials avaiable on custom orders</li>
      <li>Custom height modification</li>
      <li>Liquid spary systems</li>
      <li>(VFD) Variable Frequency Drives</li>
      <li>Leg extensions</li>
    </ul>
  </div>

  <div class="photo" role="img" aria-label="Spoons of assorted ground spices on a dark surface" style="left:16px;top:279px;width:102px;height:102px;background:radial-gradient(circle at 45% 55%,#d2692a,#8a3a1c 55%,#2b2e33)"></div>
  <div class="machine" role="img" aria-label="Stainless steel ribbon blender on a wheeled frame with control panel" style="left:123px;top:252px;width:161px;height:174px"></div>
  <div class="photo" role="img" aria-label="Spoons of colourful herbs and spices on a dark surface" style="left:285px;top:279px;width:102px;height:102px;background:radial-gradient(circle at 50% 60%,#c88a2a,#5f7a3a 50%,#23313a)"></div>

  <svg class="band band--bottom" viewBox="0 0 401 80" preserveAspectRatio="none" aria-hidden="true">
    <path d="M0 58C120 78 260 60 401 18V80H0Z" fill="var(--blue-deep)"/>
    <path d="M0 52C120 72 260 54 401 12" fill="none" stroke="var(--blue-mid)" stroke-width="1.2"/>
  </svg>

  <table class="spec spec--blenders">
    <tr><td>Model Size</td><td>5cf</td><td>7CF</td><td>10.5CF</td><td>17.5CF</td><td>35CF</td><td>53CF</td><td>70.5CF</td><td>106CF</td></tr>
    <tr><td>Working Liters</td><td>120L</td><td>200L</td><td>300L</td><td>500L</td><td>1000L</td><td>1500L</td><td>2000L</td><td>3000L</td></tr>
    <tr><td>Fill Capcity</td><td>5CF / 150L</td><td>9CF / 250L</td><td>13CF / 375L</td><td>22CF / 625L</td><td>44CF / 1250L</td><td>66CF / 1875L</td><td>88CF / 2500L</td><td>132CF / 3750L</td></tr>
    <tr><td>Weight</td><td>440lbs</td><td>550lbs</td><td>770lbs</td><td>1212lbs</td><td>1874lbs</td><td>2645lbs</td><td>3527lbs</td><td>5511lbs</td></tr>
    <tr><td>Motor Size</td><td>4hp</td><td>5.3hp</td><td>6.7hp</td><td>10hp</td><td>14.75hp</td><td>20hp</td><td>25hp</td><td>30hp</td></tr>
    <tr><td>Total Length</td><td>50"</td><td>53.5"</td><td>63"</td><td>72"</td><td>94"</td><td>102"</td><td>131.5"</td><td>157.5"</td></tr>
    <tr><td>Total Width</td><td>28"</td><td>34"</td><td>41.5"</td><td>45"</td><td>52"</td><td>66"</td><td>52.5"</td><td>54"</td></tr>
    <tr><td>Total Height</td><td>66"</td><td>69"</td><td>71"</td><td>82"</td><td>87"</td><td>95"</td><td>76"</td><td>110"</td></tr>
    <tr><td>Tub Length</td><td>31.5"</td><td>35.5"</td><td>41"</td><td>47"</td><td>59"</td><td>70"</td><td>75"</td><td>100"</td></tr>
    <tr><td>Tub Width</td><td>16.5"</td><td>22"</td><td>25"</td><td>27.5"</td><td>35.5"</td><td>39"</td><td>48"</td><td>48"</td></tr>
    <tr><td>Tub Height</td><td>20.5"</td><td>26"</td><td>28"</td><td>33"</td><td>41"</td><td>46"</td><td>51"</td><td>53"</td></tr>
    <tr><td>Shaft Diameter</td><td>2"</td><td>2-1/4"</td><td>2-5/8"</td><td>3"</td><td>3.5"</td><td>4"</td><td>4"</td><td>5-1/4"</td></tr>
    <tr><td>Tub Thickness</td><td>3mm</td><td>3mm</td><td>3mm</td><td>4mm</td><td>4mm</td><td>5mm</td><td>5mm</td><td>6mm</td></tr>
    <tr><td>Ribbon Thickness</td><td>6mm</td><td>8mm</td><td>8mm</td><td>8mm</td><td>10mm</td><td>12mm</td><td>12mm</td><td>14mm</td></tr>
    <tr><td>Max RPM</td><td>46 rpm</td><td>46 rpm</td><td>46 rpm</td><td>46 rpm</td><td>30 rpm</td><td>31 rpm</td><td>32 rpm</td><td>33 rpm</td></tr>
  </table>
</section>

<section class="page page--feeders">
  <svg class="band band--top" viewBox="0 0 401 70" preserveAspectRatio="none" aria-hidden="true">
    <path d="M0 0H401V20C300 40 230 60 150 48C90 40 40 24 0 26Z" fill="var(--blue-deep)"/>
    <path d="M0 28C40 22 90 40 150 50C230 62 300 44 401 24" fill="none" stroke="var(--blue-mid)" stroke-width="1.2"/>
  </svg>
  <div class="brand"><span class="brand__dot"></span>KEELWORTH</div>
  <h1 class="title">AUGER HOPPERS / SCREW FEEDERS</h1>

  <div class="card card--round" style="left:146px;top:107px">
    <h3>STANDARD FEATURES</h3>
    <ul>
      <li>Direct Drive</li>
      <li>304 Stainless Steel Construction</li>
      <li>Stainless Steel Safety grating</li>
      <li>Pre-wired control panel</li>
      <li>Electric Vibrator</li>
      <li>Castor Wheels</li>
    </ul>
  </div>
  <div class="card card--round" style="left:283px;top:107px">
    <h3>OPTIONS</h3>
    <ul>
      <li>Square or round hopper 3.5cf and 7cf hopper are standard</li>
      <li>Custom hoppers upto 200cf</li>
      <li>VFD (Variable Frequency Drive)</li>
      <li>Clamshell Auger Tube for easy cleanout</li>
      <li>316 Stainless Steel Construction</li>
    </ul>
  </div>

  <div class="machine" role="img" aria-label="Stainless steel auger hopper with inclined screw feeder tube on a wheeled stand" style="left:195px;top:245px;width:150px;height:140px"></div>
  <div class="photo" role="img" aria-label="Bowl of curry powder with garlic and chili" style="left:19px;top:184px;width:80px;height:80px;background:radial-gradient(circle at 50% 55%,#c08a30,#6a3b1e 55%,#1e2226)"></div>
  <div class="photo" role="img" aria-label="Bowls of orange and yellow spice powders with cloves" style="left:36px;top:271px;width:94px;height:94px;background:radial-gradient(circle at 50% 50%,#e0702a,#c9a56a 55%,#6b5a48)"></div>
  <div class="photo" role="img" aria-label="Assorted spice bowls with paprika, herbs, cinnamon and peppercorns" style="left:89px;top:356px;width:112px;height:112px;background:radial-gradient(circle at 50% 45%,#c9482a,#8a6a3a 55%,#5a3a2a)"></div>

  <svg class="band band--bottom" viewBox="0 0 401 80" preserveAspectRatio="none" aria-hidden="true">
    <path d="M0 58C120 78 260 60 401 18V80H0Z" fill="var(--blue-deep)"/>
    <path d="M0 52C120 72 260 54 401 12" fill="none" stroke="var(--blue-mid)" stroke-width="1.2"/>
  </svg>

  <table class="spec spec--feeders">
    <tr><td>MODEL</td><td>AH-A2</td><td>AH-A3</td><td>AH-A5</td><td>AH-A7</td><td>AH-A8</td><td>AH-A12</td></tr>
    <tr><td>FEEDING RATE</td><td>2m³/Hr</td><td>3m³/Hr</td><td>5m³/Hr</td><td>7m³/Hr</td><td>8m³/Hr</td><td>12m³/Hr</td></tr>
    <tr><td>PIPE DIAMETER</td><td>4"</td><td>4-1/2"</td><td>5-1/2"</td><td>6-1/4"</td><td>6-1/2"</td><td>8-1/2"</td></tr>
    <tr><td>HOPPER VOL.</td><td>3.5CF</td><td class="c" colspan="5">7CF</td></tr>
    <tr><td>DIMENSIONS</td><td>28.6"x24.4"x31.5"</td><td class="c" colspan="5">40" x 32" x 35"</td></tr>
    <tr><td>TOTAL WEIGHT</td><td>221LBS</td><td>287LBS</td><td>397LBS</td><td>441LBS</td><td>485LBS</td><td>596LBS</td></tr>
    <tr><td>CHARGING HEIGHT</td><td class="c" colspan="6">STANDARD 72 INCHES. (40" - 196" AVAILABLE)</td></tr>
    <tr><td>CHARGING ANGLE</td><td class="c" colspan="6">STANDARD 45° &nbsp;&nbsp; (30°-60° AVAILABLE)</td></tr>
  </table>
</section>

</body>
</html>
```